Luxury Business Card Design for High-End Window Treatments

Gilded Slatworks
Custom Plantation Shutters & Architectural Shading Systems

⸻

BACK

Daniel Trevick
Owner

Custom Interior & Exterior Window Treatments

919-555-0148
gildedslatworks.com

I have included a picture that I’m hoping we can use on the back, but I’m also wondering if you can get rid of the ladder? Should we get rid of shutters , shades and blinds underneath Gilded Slatworks?

Target Market(s)

High-end residential homeowners, custom home builders, architects, interior designers, and luxury renovation clients seeking premium plantation shutters and motorized architectural shading systems.

Industry/Entity Type

Custom Window treatments

Contact Information for Business Card

Front Gilded Slatworks Custom Plantation Shutters Motorized Architectural Shading Systems BACK Daniel Trevick Owner 919-555-0148 GildedSlatworks.com Custom Interior & Exterior Window Treatments By Appointment

Requirements
Nice to have
• Not 100% sure on nice to halves or the color but you can definitely check out my website to get a better understanding of what I’m trying to do

```html
<!DOCTYPE html>
<html lang="en">
<head>
<meta charset="utf-8">
<title>Gilded Slatworks — Business Card</title>
<link rel="stylesheet" href="https://fonts.googleapis.com/css2?family=Libre+Baskerville:wght@400;700&family=Lato:wght@400;700;900&display=swap">
<style>
  :root {
    --backdrop: #2a2a2a;
    --card: #0b0b0b;
    --card-edge: #161616;
    --gold: #f4c84e;
    --white: #f2f2f2;
    --silver: #cfcfcf;
    --accent-bar: #e4ddd3;
    --label-bg: #ffffff;
    --label-ink: #111111;
  }
  * { margin: 0; padding: 0; box-sizing: border-box; }
  html, body {
    width: 1200px; height: 939px; overflow: hidden;
    background: var(--backdrop);
  }
  .stage {
    width: 1200px; height: 939px;
    display: flex; flex-direction: column; align-items: center; justify-content: center;
    gap: 44px;
  }
  .card {
    position: relative;
    width: 640px; height: 366px;
    background: linear-gradient(160deg, var(--card-edge), var(--card) 60%);
    border-radius: 24px;
    overflow: hidden;
  }

  /* Front */
  .front .brand {
    position: absolute; left: 0; right: 0; top: 104px;
    text-align: center;
    font-family: "Libre Baskerville", serif;
    font-size: 40px; line-height: 1.15;
    color: var(--silver);
  }
  .front .product-line {
    position: absolute; left: 0; right: 0; top: 212px;
    display: flex; justify-content: center; gap: 22px;
    font-family: "Libre Baskerville", serif; font-weight: 700;
    font-size: 20px; color: var(--gold);
  }
  .front .tagline {
    position: absolute; left: 0; right: 0; bottom: 40px;
    text-align: center;
    font-family: "Libre Baskerville", serif;
    font-size: 13px; letter-spacing: 0.3px; color: var(--white);
  }

  /* Back */
  .back .accent-bar {
    position: absolute; left: 40px; top: 222px;
    width: 12px; height: 96px; background: var(--accent-bar);
  }
  .back .brand {
    position: absolute; left: 70px; top: 52px;
    font-family: "Libre Baskerville", serif;
    font-size: 28px; line-height: 1.2; color: var(--silver);
  }
  .back .person {
    position: absolute; left: 70px; top: 160px;
  }
  .back .name {
    font-family: "Libre Baskerville", serif; font-weight: 700;
    font-size: 23px; color: var(--gold);
  }
  .back .role {
    font-family: "Lato", sans-serif; font-size: 15px; color: var(--white);
    margin: 6px 0 0 8px;
  }
  .back .contacts {
    list-style: none; margin: 10px 0 0 8px;
    font-family: "Lato", sans-serif; font-size: 15px; color: var(--white);
  }
  .back .contacts li { display: flex; align-items: center; gap: 8px; height: 22px; }
  .back .contacts svg { width: 13px; height: 13px; flex: none; }
  .back .services {
    position: absolute; left: 78px; top: 290px;
    font-family: "Libre Baskerville", serif; font-weight: 700;
    font-size: 15px; line-height: 1.3; color: var(--gold);
    text-transform: uppercase;
  }

  .gallery {
    position: absolute; right: 16px; top: 14px;
    width: 232px; height: 338px;
    display: grid;
    grid-template-columns: 1fr 1fr;
    grid-template-rows: 104px 104px 1fr;
    gap: 8px;
  }
  .tile { position: relative; border-radius: 3px; overflow: hidden; }
  .tile.wide { grid-column: 1 / 3; }
  .tile .label {
    position: absolute; left: 0; right: 0; bottom: 0;
    background: var(--label-bg); color: var(--label-ink);
    font-family: "Lato", sans-serif; font-weight: 900;
    font-size: 10px; letter-spacing: 0.8px; text-align: center;
    padding: 4px 0 3px;
  }
  .photo-shutters { background: linear-gradient(160deg, #e9e4da, #bdb3a3); }
  .photo-blinds   { background: linear-gradient(170deg, #d9d6d1, #a8a49e); }
  .photo-shades   { background: linear-gradient(160deg, #4a4f54, #9a9486); }
  .photo-drapes   { background: linear-gradient(90deg, #55565a, #f1f1f1 45%, #f1f1f1 60%, #505155); }
  .photo-exterior { background: linear-gradient(180deg, #6fa4d8 0%, #b7cfe6 35%, #e6e2d8 55%, #5f6f4c 85%, #c7c3bb 100%); }
</style>
</head>
<body>
<main class="stage">

  <section class="card front" aria-label="Card front">
    <div class="brand">Gilded<br>Slatworks</div>
    <div class="product-line"><span>Shutters</span><span>Shades</span><span>Blinds</span></div>
    <p class="tagline">Custom Plantation Shutters &amp; Motorized Architectural Shading Systems</p>
  </section>

  <section class="card back" aria-label="Card back">
    <div class="accent-bar"></div>
    <div class="brand">Gilded<br>Slatworks</div>
    <div class="person">
      <div class="name">Daniel Trevick</div>
      <div class="role">Owner</div>
      <ul class="contacts">
        <li>
          <svg viewBox="0 0 24 24" aria-hidden="true"><path fill="#f4c84e" d="M6.6 10.8a15.1 15.1 0 0 0 6.6 6.6l2.2-2.2a1 1 0 0 1 1-.25 11.4 11.4 0 0 0 3.6.57 1 1 0 0 1 1 1V20a1 1 0 0 1-1 1A17 17 0 0 1 3 4a1 1 0 0 1 1-1h3.5a1 1 0 0 1 1 1c0 1.25.2 2.45.57 3.57a1 1 0 0 1-.25 1z"/></svg>
          919-555-0148
        </li>
        <li>
          <svg viewBox="0 0 24 24" aria-hidden="true"><circle cx="12" cy="12" r="10" fill="#f4c84e"/><path d="M2 12h20M12 2c3 3 3 17 0 20M12 2c-3 3-3 17 0 20" stroke="#0b0b0b" stroke-width="1.6" fill="none"/></svg>
          gildedslatworks.com
        </li>
      </ul>
    </div>
    <p class="services">Custom Interior &amp;<br>Exterior Window<br>Treatments</p>

    <div class="gallery">
      <figure class="tile photo-shutters" role="img" aria-label="Photo of white plantation shutters on arched windows"><span class="label">SHUTTERS</span></figure>
      <figure class="tile photo-blinds" role="img" aria-label="Photo of light window blinds in a living room"><span class="label">BLINDS</span></figure>
      <figure class="tile photo-shades" role="img" aria-label="Photo of dark roller shades over a window"><span class="label">SHADES</span></figure>
      <figure class="tile photo-drapes" role="img" aria-label="Photo of grey drapes framing sheer curtains"><span class="label">DRAPES</span></figure>
      <figure class="tile wide photo-exterior" role="img" aria-label="Photo of a house porch fitted with exterior screen shades"><span class="label">EXTERIOR</span></figure>
    </div>
  </section>

</main>
</body>
</html>
```